Vantor Wear and Fuel is looking for a Clothing/Supplement Online Store Website!

Must be convenient, and user friendly, with vibrant colors that catch the eye!

Target Market(s)

Athletes, and Fashion Customers

Industry/Entity Type

Fitness

Coding

Coded - Design and coding required

Number of Pages Required

3 page

Font styles to use
Decorative

Colors

Designer to choose colors to be used in the design.

Requirements
Must have
• Somewhere to feature products, features to promote discounts and make announcements.
Nice to have
• My logos on each page

```html
<!DOCTYPE html>
<html lang="en">
<head>
<meta charset="utf-8">
<title>Vantor Wear and Fuel</title>
<link href="https://fonts.googleapis.com/css2?family=Poppins:wght@300;400;500;600;700;800&family=Montserrat:wght@400;500;600;700&display=swap" rel="stylesheet">
<style>
:root{
  --navy:#0c1f45;
  --teal:#2fb39b;
  --teal-dark:#23957f;
  --ink:#333a44;
  --muted:#5d6670;
  --white:#ffffff;
  --line:#e3e6ea;
}
*{margin:0;padding:0;box-sizing:border-box}
html,body{width:1200px;height:4468px;overflow:hidden;background:var(--white)}
body{position:relative;font-family:"Montserrat",sans-serif;color:var(--ink)}
.abs{position:absolute}

/* hero */
.hero{left:0;top:0;width:1200px;height:700px;overflow:hidden}
.hero-photo{left:0;top:0;width:1200px;height:700px;background:linear-gradient(120deg,#3d5d63 0%,#6f7e80 35%,#2c3a3e 65%,#1d2a30 100%)}
.hero-shade{left:0;top:0;width:1200px;height:700px;background:linear-gradient(90deg,rgba(20,40,50,.55),rgba(20,40,50,.1) 60%,rgba(10,20,30,.3))}
.hero-cut{left:0;top:0}
.brand{left:113px;top:22px;font-family:"Poppins",sans-serif;font-weight:600;font-size:34px;letter-spacing:1px;color:var(--white)}
.nav{left:410px;top:32px;display:flex}
.nav a{font-family:"Poppins",sans-serif;font-weight:600;font-size:14px;color:var(--white);text-decoration:none;margin-right:55px}
.nav a.active{color:var(--teal)}
.hero-title{left:113px;top:194px;width:520px;font-family:"Poppins",sans-serif;font-weight:700;font-size:42px;line-height:54px;color:var(--white);text-transform:uppercase}
.hero-text{left:111px;top:316px;width:470px;font-size:15px;line-height:25px;color:var(--white)}
.pill{display:inline-flex;align-items:center;gap:10px;height:36px;padding:0 22px;border-radius:18px;font-family:"Poppins",sans-serif;font-weight:700;font-size:13px;color:var(--white);text-transform:uppercase}
.pill-navy{background:var(--navy)}
.pill-teal{background:var(--teal)}
.pill .arrow{width:14px;height:12px}
.hero-btn1{left:113px;top:398px}
.hero-btn2{left:283px;top:398px}
.hero-arrow{top:296px;width:24px;height:32px}
.frame{left:818px;top:161px;width:271px;height:307px;border:5px solid var(--white)}
.form-card{left:808px;top:192px;width:248px;height:314px;background:var(--navy);padding:34px 24px 0}
.form-card h3{font-family:"Poppins",sans-serif;font-weight:700;font-size:16px;line-height:18px;color:var(--white);text-transform:uppercase}
.form-card p{font-size:6.5px;color:var(--white);margin-top:12px;white-space:nowrap}
.form-row{display:flex;gap:10px;margin-top:14px}
.field{background:var(--white);height:22px;font-size:7px;padding:6px 8px;color:#555;text-transform:uppercase}
.field.half{flex:1}
.field.msg{height:88px;margin-top:10px}
.form-btn{margin-top:8px;height:26px;background:var(--teal);color:var(--white);font-size:7px;text-align:center;line-height:26px;text-transform:uppercase}

/* section headings */
.heading{left:0;width:1200px;text-align:center;font-family:"Poppins",sans-serif;font-size:38px;text-transform:uppercase;color:var(--navy)}
.heading b{font-weight:700}
.heading span{font-weight:300;color:var(--teal)}
.body-copy{left:225px;width:750px;text-align:center;font-size:14.5px;line-height:36px;color:var(--ink)}
.center-btn{left:526px;width:148px;justify-content:center}

/* products */
.card{top:1306px;width:306px;height:380px;background:var(--white);box-shadow:0 3px 10px rgba(0,0,0,.12)}
.card-photo{left:0;top:0;width:306px;height:177px}
.card-curve{left:0;top:118px}
.card h4{position:absolute;top:210px;left:0;width:306px;text-align:center;font-family:"Poppins",sans-serif;font-weight:600;font-size:17px;color:var(--navy);text-transform:uppercase}
.card p{position:absolute;top:248px;left:40px;width:226px;text-align:center;font-size:13px;line-height:21px;color:var(--muted)}
.card-btn{position:absolute;left:154px;top:336px;width:138px;height:44px;background:var(--teal);color:var(--white);border-radius:22px 22px 0 22px;font-family:"Poppins",sans-serif;font-weight:500;font-size:15px;text-align:center;line-height:44px;text-transform:uppercase}
.slide-arrow{top:1462px;width:20px;height:30px}

/* shopping */
.shop-band{left:0;top:1821px;width:1200px;height:841px}
.shop-title{color:var(--white);font-weight:700}
.shop-copy{color:var(--white)}

/* supplements */
.supp{width:224px}
.supp-photo{width:224px;height:331px;position:relative}
.sale{position:absolute;right:8px;top:14px;background:var(--navy);color:var(--white);font-size:10px;font-weight:600;padding:2px 6px}
.supp h5{text-align:center;font-size:11px;font-weight:700;color:var(--navy);margin-top:25px}
.supp .price{text-align:center;font-size:9px;font-weight:600;color:var(--navy);margin-top:6px}

/* newsletter */
.news{left:0;top:3745px;width:1200px;height:472px;background:linear-gradient(160deg,#38b9a1,var(--teal) 50%,#28a58d)}
.news-text{left:0;width:1200px;text-align:center;top:3952px;font-size:15px;color:var(--white)}
.news-field{top:4019px;height:54px;background:var(--white);font-size:15px;color:#9aa1a8;padding:18px 28px}
.news-btn{top:4019px;height:54px;background:var(--navy);color:#c9cfe0;font-size:15px;padding:18px 28px}

/* footer */
.foot-brand{left:113px;top:4290px;font-family:"Poppins",sans-serif;font-weight:600;font-size:52px;letter-spacing:1px;color:var(--navy)}
.foot-links{right:142px;top:4282px;text-align:right}
.foot-links a{display:block;font-size:12px;color:var(--navy);text-decoration:none;text-transform:uppercase;margin-bottom:26px}
.social{top:4410px;width:18px;height:18px;background:var(--navy);border-radius:3px}
.copyright{left:0;width:1200px;top:4430px;text-align:center;font-size:11px;color:var(--navy);text-transform:uppercase}
</style>
</head>
<body>

<!-- HERO -->
<section class="abs hero">
  <div class="abs hero-photo" role="img" aria-label="Athlete drinking from a bottle at an outdoor training ground"></div>
  <div class="abs hero-shade"></div>
  <svg class="abs hero-cut" width="1200" height="700" viewBox="0 0 1200 700">
    <polygon points="0,468 298,628 590,541 928,694 1200,551 1200,700 0,700" fill="#ffffff"/>
    <polyline points="0,468 298,628 590,541 928,694 1200,551" fill="none" stroke="#2fb39b" stroke-width="12"/>
  </svg>
</section>

<div class="abs brand">VANTOR</div>
<nav class="abs nav">
  <a class="active" href="#">HOME</a>
  <a href="#">ABOUT US</a>
  <a href="#">SERVICES</a>
  <a href="#">PRODUCTS</a>
  <a href="#">BLOG</a>
  <a href="#">CONTACT</a>
</nav>

<h1 class="abs hero-title">Vantor Wear and Fuel</h1>
<p class="abs hero-text">Lorem ipsum dolor sit amet, consectetur adipiscing elit, sed do eiusmod tempor incididunt</p>
<div class="abs pill pill-navy hero-btn1">Get Started
  <svg class="arrow" viewBox="0 0 14 12"><path d="M1 6 H12 M8 2 L12 6 L8 10" stroke="#2fb39b" stroke-width="2" fill="none"/></svg></div>
<div class="abs pill pill-teal hero-btn2">50% Vantor
  <svg class="arrow" viewBox="0 0 14 12"><path d="M1 6 H12 M8 2 L12 6 L8 10" stroke="#0c1f45" stroke-width="2" fill="none"/></svg></div>

<svg class="abs hero-arrow" style="left:52px" viewBox="0 0 24 32"><polyline points="16,6 6,16 16,26" fill="none" stroke="#fff" stroke-width="3"/></svg>
<svg class="abs hero-arrow" style="left:1128px" viewBox="0 0 24 32"><polyline points="8,6 18,16 8,26" fill="none" stroke="#fff" stroke-width="3"/></svg>

<div class="abs frame"></div>
<form class="abs form-card">
  <h3>Lorem ipsum<br>dolor sit amet,</h3>
  <p>Send us a short note and we will reply soon</p>
  <div class="form-row"><div class="field half">Name</div><div class="field half">Email</div></div>
  <div class="field msg">Message</div>
  <div class="form-btn">Contact</div>
</form>

<!-- ABOUT -->
<h2 class="abs heading" style="top:724px"><b>About</b> <span>Us</span></h2>
<p class="abs body-copy" style="top:817px">Lorem ipsum dolor sit amet, consectetur adipiscing elit, sed do eiusmod tempor incididunt ut labore et dolore magna aliqua. Quis ipsum suspendisse ultrices gravida. Risus commodo viverra maecenas accumsan lacus vel facilisis. Lorem ipsum dolor sit amet, consectetur adipiscing elit, sed do eiusmod tempor incididunt ut labore et dolore magna aliqua. Quis ipsum suspendisse ultrices gravida. Risus commodo viverra maecenas accumsan lacus vel facilisis.</p>
<div class="abs pill pill-navy center-btn" style="top:1056px">Read More
  <svg class="arrow" viewBox="0 0 14 12"><path d="M1 6 H12 M8 2 L12 6 L8 10" stroke="#2fb39b" stroke-width="2" fill="none"/></svg></div>

<!-- FEATURED PRODUCTS -->
<h2 class="abs heading" style="top:1183px"><b>Featured</b> <span>Products</span></h2>
<svg class="abs slide-arrow" style="left:58px" viewBox="0 0 20 30"><polyline points="15,4 5,15 15,26" fill="none" stroke="#2fb39b" stroke-width="3"/></svg>
<svg class="abs slide-arrow" style="left:1128px" viewBox="0 0 20 30"><polyline points="5,4 15,15 5,26" fill="none" stroke="#2fb39b" stroke-width="3"/></svg>

<article class="abs card" style="left:113px">
  <div class="abs card-photo" role="img" aria-label="Black hoodie shown front and back" style="background:linear-gradient(90deg,#f3f3f3,#1a1a1a 30%,#2a2a2a 70%,#eee)"></div>
  <svg class="abs card-curve" width="306" height="70" viewBox="0 0 306 70"><path d="M0 70 L0 60 Q160 60 306 0 L306 70 Z" fill="#0c1f45"/><path d="M0 70 Q170 68 306 14 L306 70 Z" fill="#fff"/></svg>
  <h4>Lorem Ipsum</h4>
  <p>Lorem Ipsum is simply dummy text of the printing and typesetting industry.</p>
  <div class="card-btn">Read More</div>
</article>
<article class="abs card" style="left:446px">
  <div class="abs card-photo" role="img" aria-label="White t-shirt shown front and back" style="background:linear-gradient(90deg,#cfcfcf,#f7f7f7 30%,#f2f2f2 70%,#d5d5d5)"></div>
  <svg class="abs card-curve" width="306" height="70" viewBox="0 0 306 70"><path d="M0 70 L0 60 Q160 60 306 0 L306 70 Z" fill="#0c1f45"/><path d="M0 70 Q170 68 306 14 L306 70 Z" fill="#fff"/></svg>
  <h4>Lorem Ipsum</h4>
  <p>Lorem Ipsum is simply dummy text of the printing and typesetting industry.</p>
  <div class="card-btn">Read More</div>
</article>
<article class="abs card" style="left:780px">
  <div class="abs card-photo" role="img" aria-label="Black printed t-shirt on a model" style="background:linear-gradient(90deg,#e8e8e8,#1c1c1c 20%,#222 80%,#eaeaea)"></div>
  <svg class="abs card-curve" width="306" height="70" viewBox="0 0 306 70"><path d="M0 70 L0 60 Q160 60 306 0 L306 70 Z" fill="#0c1f45"/><path d="M0 70 Q170 68 306 14 L306 70 Z" fill="#fff"/></svg>
  <h4>Lorem Ipsum</h4>
  <p>Lorem Ipsum is simply dummy text of the printing and typesetting industry.</p>
  <div class="card-btn">Read More</div>
</article>

<!-- SHOPPING -->
<section class="abs shop-band">
  <svg width="1200" height="841" viewBox="0 0 1200 841" role="img" aria-label="Clothes hanging on a rail in a store" style="position:absolute;left:0;top:0">
    <defs><linearGradient id="shopFade" x1="0" y1="0" x2="0" y2="1">
      <stop offset="0" stop-color="#2b3340"/><stop offset=".45" stop-color="#4a5260"/><stop offset=".8" stop-color="#b9bcc2"/><stop offset="1" stop-color="#ffffff"/></linearGradient></defs>
    <polygon points="0,130 298,69 590,147 928,0 1200,138 1200,841 0,841" fill="url(#shopFade)"/>
  </svg>
</section>
<h2 class="abs heading shop-title" style="top:2045px">Shopping</h2>
<p class="abs body-copy shop-copy" style="top:2140px">Lorem ipsum dolor sit amet, consectetur adipiscing elit, sed do eiusmod tempor incididunt ut labore et dolore magna aliqua. Quis ipsum suspendisse ultrices gravida. Risus commodo viverra maecenas accumsan lacus vel facilisis. Lorem ipsum dolor sit amet, consectetur adipiscing elit, sed do eiusmod tempor incididunt ut labore et dolore magna aliqua. Quis ipsum suspendisse ultrices gravida. Risus commodo viverra maecenas accumsan lacus vel facilisis.</p>
<div class="abs pill pill-navy center-btn" style="top:2393px">Shop Now
  <svg class="arrow" viewBox="0 0 14 12"><path d="M1 6 H12 M8 2 L12 6 L8 10" stroke="#2fb39b" stroke-width="2" fill="none"/></svg></div>

<!-- SUPPLEMENT -->
<h2 class="abs heading" style="top:2645px;font-weight:700">Supplement</h2>

<div class="abs supp" style="left:241px;top:2792px">
  <div class="supp-photo" role="img" aria-label="Vitamin bottle on red background" style="background:linear-gradient(135deg,#ee3f36,#e9332d)"><span class="sale">Sale</span></div>
  <h5>Lorem Ipsum</h5><div class="price">$45.00 $60.00</div>
</div>
<div class="abs supp" style="left:487px;top:2792px">
  <div class="supp-photo" role="img" aria-label="Capsule bottle on blue background" style="background:linear-gradient(135deg,#5aaee6,#3d9be0)"></div>
  <h5>Lorem Ipsum</h5><div class="price">$45.00 $60.00</div>
</div>
<div class="abs supp" style="left:735px;top:2792px">
  <div class="supp-photo" role="img" aria-label="Protein tub on dark background" style="background:linear-gradient(180deg,#3a2f2a,#6b5e56 50%,#2c2521)"><span class="sale">Sale</span></div>
  <h5>Lorem Ipsum</h5><div class="price">$45.00 $60.00</div>
</div>
<div class="abs supp" style="left:241px;top:3229px">
  <div class="supp-photo" role="img" aria-label="Shaker bottle with powder scoop" style="background:linear-gradient(180deg,#2a2d34,#4a3f3a 60%,#8a7d72)"><span class="sale">Sale</span></div>
  <h5>Lorem Ipsum</h5><div class="price">$45.00 $60.00</div>
</div>
<div class="abs supp" style="left:487px;top:3229px">
  <div class="supp-photo" role="img" aria-label="White supplement tub with lid" style="background:linear-gradient(180deg,#3b3d42,#dcdcdc 40%,#f2f2f2)"><span class="sale">Sale</span></div>
  <h5>Lorem Ipsum</h5><div class="price">$45.00 $60.00</div>
</div>
<div class="abs supp" style="left:735px;top:3229px">
  <div class="supp-photo" role="img" aria-label="Black protein tub with shaker and scoop" style="background:linear-gradient(180deg,#f4f4f4,#222 30%,#1a1a1a 75%,#f1f1f1);outline:1px solid #e3e6ea"></div>
  <h5>Lorem Ipsum</h5><div class="price">$45.00 $60.00</div>
</div>

<!-- NEWSLETTER -->
<section class="abs news" role="img" aria-label="Teal background with scattered capsules"></section>
<h2 class="abs heading" style="top:3880px;color:#fff"><b>Newsletter</b> <span style="color:#fff;font-weight:300">Sign-Up</span></h2>
<p class="abs news-text">Lorem ipsum dolor sit amet, consectetur adipiscing elit, sed</p>
<div class="abs news-field" style="left:146px;width:232px">First Name</div>
<div class="abs news-field" style="left:390px;width:234px">Last Name</div>
<div class="abs news-field" style="left:638px;width:232px">Email-Address</div>
<div class="abs news-btn" style="left:881px;width:173px">Sign Up</div>

<!-- FOOTER -->
<div class="abs foot-brand">VANTOR</div>
<nav class="abs foot-links">
  <a href="#">About</a>
  <a href="#">Journeys</a>
  <a href="#">Get Started</a>
</nav>
<div class="abs social" style="left:968px"></div>
<div class="abs social" style="left:1002px"></div>
<div class="abs social" style="left:1037px"></div>
<p class="abs copyright">© Copy Rights Reserved @ 2019. All Rights Reserved</p>

</body>
</html>
```